BOLD & MINIMALIST DESIGN NEEDED

We want a very bold but minimalistic business card design that is impactful and utilizes both sides of the business card. Our current logo is included for your use.

We want bold fonts and good use of negative space. We don't want the logo to overpower the design.

Target Market(s)

Professionals who are building new commercial buildings.

Industry/Entity Type

Construction

Contact Information for Business Card

Name, Title, email, office phone, cell phone, website

Font styles to use
Serif
Sans Serif

Requirements
Must have
• Bold design!

```html
<!DOCTYPE html>
<html lang="en">
<head>
<meta charset="utf-8">
<title>Ridgepoint Build Co – Business Card</title>
<link rel="stylesheet" href="https://fonts.googleapis.com/css2?family=Noto+Serif:wght@700&family=Fira+Sans:wght@600&display=swap">
<style>
  :root {
    --backdrop: #cbcbcb;
    --card: #ffffff;
    --accent: #00ff00;
    --ink: #0a0a0a;
    --edge: #2a2a2a;
  }
  html, body {
    margin: 0;
    padding: 0;
    width: 1200px;
    height: 1200px;
    overflow: hidden;
    background: var(--backdrop);
  }
  .card {
    position: absolute;
    left: 215px;
    width: 774px;
    height: 425px;
    border-radius: 30px;
    overflow: hidden;
    background: var(--card);
    box-shadow: 2px 3px 0 var(--edge), 4px 6px 8px rgba(0,0,0,0.25);
  }
  .card--front { top: 148px; }
  .card--back { top: 614px; }
  .card svg { display: block; width: 100%; height: 100%; }
  .accent-fill { fill: var(--accent); }
  .ink-fill { fill: var(--ink); }
  .serif { font-family: "Noto Serif", Georgia, serif; font-weight: 700; }
  .sans { font-family: "Fira Sans", Arial, sans-serif; font-weight: 600; }
  .name { font-size: 80px; fill: var(--ink); }
  .name-first { fill: var(--accent); }
  .title { font-size: 50px; fill: var(--ink); }
  .contact { font-size: 58px; fill: var(--ink); }
  .brand { fill: var(--ink); }
  .rule { stroke: var(--accent); stroke-width: 4; }
</style>
</head>
<body>

<div class="card card--front">
  <svg viewBox="0 0 1246 684" xmlns="http://www.w3.org/2000/svg">
    <path class="accent-fill" d="M0 95 L415 164 Q500 182 492 255 L410 684 L0 684 Z"/>

    <g class="brand-lockup">
      <rect class="ink-fill" x="211" y="250" width="40" height="40"/>
      <text class="serif brand" x="231" y="370" font-size="62" text-anchor="middle">RIDGEPOINT</text>
      <text class="serif brand" x="231" y="430" font-size="42" text-anchor="middle">BUILD CO</text>
    </g>

    <text class="serif name" x="563" y="162"><tspan class="name-first">Your</tspan> Name Here</text>
    <text class="sans title" x="565" y="232">Your Title Here</text>
    <line class="rule" x1="568" y1="256" x2="1246" y2="256"/>

    <g class="icon icon-person ink-fill">
      <circle cx="587" cy="302" r="10"/>
      <path d="M566 340 Q566 314 587 314 Q608 314 608 340 Z"/>
    </g>
    <text class="serif contact" x="633" y="340">(555) 014-2270</text>

    <g class="icon icon-mobile">
      <rect class="ink-fill" x="571" y="392" width="32" height="50" rx="5"/>
      <rect x="582" y="431" width="10" height="4" rx="2" fill="#fff"/>
    </g>
    <text class="serif contact" x="633" y="442">1-800-555-0199</text>

    <g class="icon icon-mail">
      <rect class="ink-fill" x="561" y="498" width="50" height="36" rx="4"/>
      <path d="M561 502 L586 522 L611 502" fill="none" stroke="#fff" stroke-width="4"/>
    </g>
    <text class="serif contact" x="633" y="530">info@ridgepnt.com</text>

    <g class="icon icon-globe" fill="none" stroke="var(--ink)" stroke-width="6">
      <circle cx="586" cy="608" r="23"/>
      <ellipse cx="586" cy="608" rx="9" ry="23"/>
      <line x1="563" y1="608" x2="609" y2="608"/>
    </g>
    <text class="serif contact" x="633" y="624">www.ridgepnt.com</text>
  </svg>
</div>

<div class="card card--back">
  <svg viewBox="0 0 1246 684" xmlns="http://www.w3.org/2000/svg">
    <path class="accent-fill" d="M836 0 L1246 0 L1246 590 L836 520 Q750 505 753 425 Z" stroke="var(--edge)" stroke-width="1.5"/>

    <g class="brand-lockup">
      <rect class="accent-fill" x="380" y="220" width="50" height="50"/>
      <text class="serif brand" x="405" y="380" font-size="84" text-anchor="middle">RIDGEPOINT</text>
      <text class="serif brand" x="405" y="460" font-size="56" text-anchor="middle">BUILD CO</text>
    </g>

    <text class="serif contact" x="416" y="577" font-size="62" text-anchor="middle">www.ridgepnt.com</text>
  </svg>
</div>

</body>
</html>
```